Spiritual Healing bussiness needs logo/business card

Simple, clean looking logo/card
For spiritual business with healing services and occult rituals

Contact Information for Business Card

Needs my name: Tobin Varley
Business name: Lantern Healing Shop
Services provided and worded in this way:

Reiki Healing
Tarot
Oils
Rituals Of Change

Can look occult like but with light energy.

Colors
0255a3
3276b5
85abd2
33a6d7
85cae6
0292cd

```html
<!DOCTYPE html>
<html lang="en">
<head>
<meta charset="utf-8">
<title>Lantern Healing Shop – Business Card</title>
<link href="https://fonts.googleapis.com/css2?family=Arvo:wght@400;700&family=Lato:wght@400;700&display=swap" rel="stylesheet">
<style>
  :root {
    --navy: #0255a3;
    --mid-blue: #3276b5;
    --soft-blue: #85abd2;
    --sky: #33a6d7;
    --pale-sky: #85cae6;
    --bright: #0292cd;
    --paper: #efefef;
    --ink: #2a2a2a;
    --table: #3a3b3d;
  }
  * { box-sizing: border-box; margin: 0; padding: 0; }
  html, body { width: 1200px; height: 896px; overflow: hidden; }
  body {
    background: var(--table);
    display: flex;
    flex-direction: column;
    align-items: center;
    justify-content: center;
    gap: 56px;
    font-family: 'Lato', sans-serif;
  }
  .card {
    position: relative;
    width: 600px;
    height: 343px;
    overflow: hidden;
    box-shadow: 0 10px 30px rgba(0,0,0,0.35);
  }
  /* Front */
  .card-front {
    background: radial-gradient(ellipse at 30% 20%, var(--bright) 0%, #0177c4 45%, var(--navy) 100%);
    color: #fff;
  }
  .card-front .business-name {
    position: absolute;
    left: 60px;
    top: 110px;
    font-family: 'Arvo', serif;
    font-size: 44px;
    font-weight: 400;
    letter-spacing: 0.5px;
  }
  .card-front .divider {
    position: absolute;
    left: 60px;
    right: 60px;
    top: 196px;
    height: 1px;
    background: rgba(255,255,255,0.4);
  }
  .services {
    position: absolute;
    left: 60px;
    top: 210px;
    display: flex;
    align-items: center;
    gap: 14px;
    font-size: 17px;
    list-style: none;
  }
  .services li + li::before {
    content: "";
    display: inline-block;
    width: 6px; height: 6px;
    border-radius: 50%;
    background: #fff;
    margin-right: 14px;
    vertical-align: middle;
  }
  /* Back */
  .card-back { background: var(--paper); }
  .card-back .edge-stripe {
    position: absolute;
    left: 0; right: 0; bottom: 0;
    height: 9px;
    background: linear-gradient(90deg, var(--navy), var(--sky));
  }
  .contact {
    position: absolute;
    left: 40px;
    top: 120px;
  }
  .person-name {
    font-family: 'Arvo', serif;
    font-size: 26px;
    color: var(--navy);
    margin-bottom: 6px;
  }
  .person-name .surname { color: var(--mid-blue); }
  .contact-line {
    display: flex;
    align-items: center;
    gap: 8px;
    font-size: 16px;
    color: var(--ink);
    line-height: 1.4;
  }
  .contact-line svg { width: 16px; height: 16px; flex: none; }
  .rule {
    position: absolute;
    height: 1px;
    background: #d6d6d6;
  }
  .rule-mid { left: 40px; right: 40px; top: 246px; }
  .brand {
    position: absolute;
    right: 40px;
    top: 110px;
    display: flex;
    flex-direction: column;
    align-items: flex-end;
    gap: 12px;
  }
  .brand-dot {
    width: 64px; height: 64px;
    border-radius: 50%;
    border: 6px solid var(--navy);
  }
  .brand-name {
    font-family: 'Arvo', serif;
    font-size: 27px;
    color: var(--navy);
  }
  .website {
    position: absolute;
    right: 40px;
    top: 266px;
    font-size: 16px;
    color: var(--navy);
  }
</style>
</head>
<body>

<section class="card card-front">
  <h1 class="business-name">Lantern Healing Shop</h1>
  <div class="divider"></div>
  <ul class="services">
    <li>Reiki Healing</li>
    <li>Tarot</li>
    <li>Oils</li>
    <li>Rituals Of Change</li>
  </ul>
</section>

<section class="card card-back">
  <div class="contact">
    <p class="person-name">Tobin <span class="surname">Varley</span></p>
    <p class="contact-line">
      <svg viewBox="0 0 16 16" aria-hidden="true"><circle cx="8" cy="8" r="7.5" fill="var(--navy)"/><path d="M5 4.5c.6-.4 1.1-.3 1.4.2l.6 1.1c.2.4 0 .8-.3 1l-.4.3c.4.9 1.1 1.6 2 2l.3-.4c.3-.3.7-.4 1-.2l1.1.6c.5.3.6.8.2 1.4-.7.9-1.8 1-3.1.2C6.3 9.9 5.2 8.6 4.8 7.3 4.4 6.1 4.4 5.1 5 4.5z" fill="#fff"/></svg>
      044-555 0192 736
    </p>
    <p class="contact-line">
      <svg viewBox="0 0 16 16" aria-hidden="true"><circle cx="8" cy="8" r="7.5" fill="var(--navy)"/><rect x="4" y="5.2" width="8" height="5.6" rx="0.6" fill="#fff"/><path d="M4.3 5.6 8 8.4l3.7-2.8" stroke="var(--navy)" stroke-width="0.9" fill="none"/></svg>
      hello@lanternmail.com
    </p>
  </div>

  <div class="brand">
    <div class="brand-dot"></div>
    <p class="brand-name">Lantern Healing Shop</p>
  </div>

  <div class="rule rule-mid"></div>
  <p class="website">www.LanternHealingShop.com</p>
  <div class="edge-stripe"></div>
</section>

</body>
</html>
```